Modern Business Card For A Digital Advertising Company

I'll be print on the Pell Prints Velour paper http://us.pellprints.com/products/velour/business-cards.html
Need's to be modern and use the color palette of the logo or gray scales. I think integrating the pixelation of the logo in to the card and having it wrap from one side to the other could be interesting. My company provides ad operations, web development, and number of other services to websites around the world. You can see my website at http://www.zantorhq.com
Contact info on the card needs to have
Owen Lasko
President
p.318.204.6637
owen@zantorhq.com
http://www.zantorhq.com
Doesn't necessarily need to be in that order
Website owners
Business

```html
<!DOCTYPE html>
<html lang="en">
<head>
<meta charset="utf-8">
<title>Zantor HQ — Business Card</title>
<link rel="stylesheet" href="https://fonts.googleapis.com/css2?family=Tinos:wght@400;700&family=Open+Sans:wght@700&display=swap">
<style>
  :root {
    --bg: #2b2b2b;
    --band-dark: #2e302c;
    --band-dark-2: #474a44;
    --paper: #ffffff;
    --green-deep: #5f8f35;
    --green: #78ad3c;
    --green-bright: #8cc63f;
    --ink: #333333;
    --white: #ffffff;
  }
  * { margin: 0; padding: 0; box-sizing: border-box; }
  html, body {
    width: 1200px; height: 757px; overflow: hidden;
    background: var(--bg);
  }
  .canvas { position: relative; width: 1200px; height: 757px; }

  .card {
    position: absolute;
    width: 520px; height: 300px;
    border-radius: 18px;
    overflow: hidden;
    box-shadow: 0 10px 24px rgba(0,0,0,.55);
  }

  /* Front */
  .card-front { left: 70px; top: 80px; background: var(--paper); }
  .front-band {
    height: 48px;
    background: linear-gradient(180deg, var(--band-dark-2), var(--band-dark));
    display: flex; align-items: flex-end; justify-content: center;
    padding-bottom: 8px;
    font-family: "Tinos", serif; color: var(--white);
  }
  .holder-name { font-weight: 700; font-size: 23px; }
  .holder-title { font-size: 16px; margin-left: 6px; }
  .front-brand {
    height: 152px;
    display: flex; align-items: center; justify-content: center; gap: 12px;
  }
  .brand-mark { width: 26px; height: 26px; background: var(--green-bright); }
  .brand-name {
    font-family: "Tinos", serif; font-weight: 700;
    font-size: 40px; color: var(--green);
  }
  .front-contact {
    height: 100px;
    background: linear-gradient(90deg, var(--green-deep), var(--green-bright));
    display: flex; flex-direction: column; align-items: center; justify-content: center; gap: 8px;
    font-family: "Tinos", serif; font-size: 15px; color: var(--white);
  }
  .contact-row { display: flex; align-items: center; gap: 14px; }
  .contact-item { display: flex; align-items: center; gap: 5px; }
  .contact-item svg { width: 12px; height: 12px; fill: var(--white); }

  /* Back */
  .card-back {
    left: 610px; top: 370px;
    background: linear-gradient(200deg, var(--green-deep) 0%, var(--green) 50%, var(--green-bright) 100%);
    display: flex; flex-direction: column; align-items: center; justify-content: center;
  }
  .back-brand { display: flex; align-items: center; gap: 14px; margin-top: -10px; }
  .back-brand .brand-mark { width: 34px; height: 34px; background: var(--white); }
  .back-brand .brand-name { color: var(--white); font-size: 54px; }
  .back-url {
    position: absolute; bottom: 34px; width: 100%; text-align: center;
    font-family: "Open Sans", sans-serif; font-weight: 700;
    font-size: 19px; letter-spacing: 1.5px; color: var(--white);
  }
</style>
</head>
<body>
<main class="canvas">

  <section class="card card-front" aria-label="Card front">
    <header class="front-band">
      <span class="holder-name">Owen Lasko,</span><span class="holder-title">President</span>
    </header>
    <div class="front-brand">
      <span class="brand-mark"></span>
      <span class="brand-name">Zantor HQ</span>
    </div>
    <footer class="front-contact">
      <div class="contact-row">
        <span class="contact-item">
          <svg viewBox="0 0 24 24" aria-hidden="true"><path d="M6.6 10.8a15.1 15.1 0 0 0 6.6 6.6l2.2-2.2c.3-.3.7-.4 1-.2 1.1.4 2.3.6 3.6.6.6 0 1 .4 1 1V20c0 .6-.4 1-1 1A17 17 0 0 1 3 4c0-.6.4-1 1-1h3.5c.6 0 1 .4 1 1 0 1.3.2 2.5.6 3.6.1.3 0 .7-.2 1z"/></svg>
          318.204.6637
        </span>
        <span class="contact-item">
          <svg viewBox="0 0 24 24" aria-hidden="true"><path d="M2 5h20v14H2z M2 5l10 8 10-8" /></svg>
          owen@zantorhq.com
        </span>
      </div>
      <div class="contact-row">
        <span class="contact-item">
          <svg viewBox="0 0 24 24" aria-hidden="true"><circle cx="12" cy="12" r="10"/></svg>
          www.zantorhq.com
        </span>
      </div>
    </footer>
  </section>

  <section class="card card-back" aria-label="Card back">
    <div class="back-brand">
      <span class="brand-mark"></span>
      <span class="brand-name">Zantor HQ</span>
    </div>
    <p class="back-url">www.zantorhq.com</p>
  </section>

</main>
</body>
</html>
```